New business card for a regional office of a US M&A company

We need business card for a finance company, office based in Hong Kong , our Head office is in US, our business is to Merge and acquires companies , the new office will be a regional office for the Asia Pacific region. We want to use the head office logo as attached ( but don't have to be exactly the same, can be a variation to it) as a base and then add Asia Pacific alongside the logo.
We would prefer to have be bilingual Eng + Chinese, although we don't really have Chinese company name .

Industry/Entity Type

Business

Contact Information for Business Card

Clara Jo Tsang
 

VP,
APAC M&A Operations
Orin Vantage Asia Pacific Limited
 
Unit 1407, K18
18 Tai Lok Shan Road, 
Hong Kong 
 
M: +852 6038 1742
T : +852 2836 4100
F : +852 2836 4177
VOIP: 4158
 
cjtsang@orinvantage.com

Font styles to use
Serif
Sans Serif

Colors

Designer to choose colors to be used in the design.

Requirements
Must have
• APAC Office

```html
<!DOCTYPE html>
<html lang="en">
<head>
<meta charset="utf-8">
<title>Orin Vantage Asia Pacific – Business Card</title>
<link rel="stylesheet" href="https://fonts.googleapis.com/css2?family=Open+Sans:wght@700&family=Roboto:wght@400&family=Roboto+Condensed:wght@700&display=swap">
<style>
  :root {
    --backdrop: #c4c4c4;
    --card-navy: #0f2a44;
    --ink-light: #e4e8ec;
    --accent-cyan: #1fa8d6;
  }
  * { margin: 0; padding: 0; box-sizing: border-box; }
  html, body {
    width: 1200px;
    height: 960px;
    overflow: hidden;
    background: var(--backdrop);
  }
  .canvas {
    position: relative;
    width: 1200px;
    height: 960px;
  }
  .card {
    position: absolute;
    width: 601px;
    height: 342px;
    background: var(--card-navy);
    color: var(--ink-light);
    font-family: "Roboto", Arial, sans-serif;
  }
  .card--front { left: 320px; top: 108px; }
  .card--back  { left: 320px; top: 493px; }

  /* Front face */
  .front-brand {
    position: absolute;
    left: 0; right: 0;
    top: 138px;
    display: flex;
    align-items: center;
    justify-content: center;
    gap: 14px;
  }
  .front-brand__square {
    width: 22px;
    height: 22px;
    background: var(--ink-light);
  }
  .front-brand__name {
    font-family: "Open Sans", Arial, sans-serif;
    font-weight: 700;
    font-size: 34px;
    letter-spacing: 0.02em;
    color: var(--ink-light);
  }
  .front-web {
    position: absolute;
    left: 0; right: 0;
    top: 284px;
    text-align: center;
    font-size: 14px;
    letter-spacing: 0.48em;
    color: var(--ink-light);
  }

  /* Back face */
  .contact {
    position: absolute;
    left: 35px;
    top: 72px;
  }
  .contact__name {
    font-family: "Roboto Condensed", "Arial Narrow", sans-serif;
    font-weight: 700;
    font-size: 21px;
    color: var(--accent-cyan);
    text-transform: uppercase;
    line-height: 24px;
  }
  .contact__title {
    margin-left: 2px;
    font-size: 15px;
    line-height: 22px;
  }
  .contact__address {
    margin-top: 8px;
    font-size: 15px;
    line-height: 18.5px;
  }
  .contact__phones {
    list-style: none;
    margin-top: 9px;
    font-size: 15px;
    line-height: 19px;
  }
  .contact__phones li {
    display: flex;
    align-items: center;
    gap: 8px;
  }
  .contact__phones svg {
    width: 14px;
    height: 14px;
    fill: var(--accent-cyan);
  }
  .contact__voip {
    margin-top: 9px;
    font-size: 15px;
  }
  .back-brand {
    position: absolute;
    left: 318px;
    width: 254px;
    top: 34px;
    display: flex;
    flex-direction: column;
    align-items: center;
    gap: 30px;
  }
  .back-brand__square {
    width: 40px;
    height: 40px;
    background: var(--ink-light);
  }
  .back-brand__name {
    font-family: "Open Sans", Arial, sans-serif;
    font-weight: 700;
    font-size: 32px;
    line-height: 36px;
    color: var(--accent-cyan);
    white-space: nowrap;
  }
</style>
</head>
<body>
<main class="canvas">

  <section class="card card--front" aria-label="Card front">
    <div class="front-brand">
      <span class="front-brand__square"></span>
      <span class="front-brand__name">ORIN VANTAGE</span>
    </div>
    <p class="front-web">www.orinvantage.com</p>
  </section>

  <section class="card card--back" aria-label="Card back">
    <div class="contact">
      <h1 class="contact__name">Clara Jo Tsang</h1>
      <p class="contact__title">VP</p>
      <p class="contact__address">
        APAC M&amp;A Operations<br>
        Orin Vantage Asia Pacific Limited<br>
        Unit 1407, K18<br>
        18 Tai Lok Shan Road<br>
        Hong Kong
      </p>
      <ul class="contact__phones">
        <li>
          <svg viewBox="0 0 16 16" aria-label="Telephone"><path d="M3.6 1.2l2.3 2.6c.3.4.3.9 0 1.3L4.8 6.4c.8 1.9 2.9 4 4.8 4.8l1.3-1.1c.4-.3.9-.3 1.3 0l2.6 2.3c.4.4.4 1 0 1.4l-1.4 1.4c-.5.5-1.3.7-2 .4C6.9 14 2 9.1.4 4.6c-.3-.7-.1-1.5.4-2l1.4-1.4c.4-.4 1-.4 1.4 0z"/></svg>
          +852 2836 4100
        </li>
        <li>
          <svg viewBox="0 0 16 16" aria-label="Mobile"><path d="M4.5 0h7c.8 0 1.5.7 1.5 1.5v13c0 .8-.7 1.5-1.5 1.5h-7C3.7 16 3 15.3 3 14.5v-13C3 .7 3.7 0 4.5 0zm.3 2v10.5h6.4V2H4.8zM8 13.3a.9.9 0 100 1.8.9.9 0 000-1.8z"/></svg>
          +852 6038 1742
        </li>
        <li>
          <svg viewBox="0 0 16 16" aria-label="Fax"><path d="M4 0h8v4H4zM1.5 5h13c.8 0 1.5.7 1.5 1.5V12h-3v4H3v-4H0V6.5C0 5.7.7 5 1.5 5zM4.5 10v4.5h7V10h-7z"/></svg>
          +852 2836 4177
        </li>
      </ul>
      <p class="contact__voip">VOIP: 4158</p>
    </div>

    <div class="back-brand">
      <span class="back-brand__square"></span>
      <span class="back-brand__name">ORIN VANTAGE</span>
    </div>
  </section>

</main>
</body>
</html>
```